Recruitment Site Design

We need a design for the login page, about page, and inner pages of a recruitment site for an oil and gas company. Design should be modern, sleek, professional and colors can be blue, green, white, orange or any other recommended colors.

Please also take into consideration that once the users login, they will need to access a form to fill in their information.

** UPDATE: Kindly provide a design for the inner information page consistent with the outer design. Attached is a picture of the basic structure. ***
Updates

Please provide a design for inner pages as shown in the design brief consistent with the registration page provided. 

Reason: We're extending it to get more inside pages.

Target Market(s)

Professionals looking for a career in the oil and gas industry in the Middle East.

Industry/Entity Type

Oil And Gas

Requirements
Must have
• Sleek design

```html
<!DOCTYPE html>
<html lang="en">
<head>
<meta charset="utf-8">
<title>Recruitment Home</title>
<link href="https://fonts.googleapis.com/css2?family=Ubuntu:wght@400;500&family=PT+Sans:wght@400;700&display=swap" rel="stylesheet">
<style>
:root{
  --page:#f3f1ef;
  --band:#f4f3f5;
  --card:#f6f5f5;
  --orange:#e4860f;
  --orange-light:#fbb543;
  --orange-dark:#d0740a;
  --text:#4a4a4a;
  --nav-text:#3d3d3d;
  --line:#dcdad8;
  --footer-top:#5e5e5e;
  --footer-bottom:#383838;
  --photo-sea:#3a6fae;
  --photo-team:#c9ccd3;
  --photo-sky:#8ea6c6;
}
*{box-sizing:border-box;margin:0;padding:0}
html,body{width:1024px;height:1200px;overflow:hidden}
body{background:var(--page);font-family:"PT Sans",sans-serif;color:var(--text);position:relative}
.abs{position:absolute}

.logo{left:0;width:1024px;top:38px;text-align:center;font-family:"Ubuntu",sans-serif;font-size:48px;color:var(--orange);font-weight:400}

.main-nav{left:119px;top:130px;height:47px;display:flex;background:linear-gradient(#f1f0ef,#e5e3e1);box-shadow:0 1px 3px rgba(0,0,0,.15);z-index:2}
.main-nav a{display:flex;align-items:center;justify-content:center;font-size:13.5px;color:var(--nav-text);text-decoration:none;border-right:1px solid #d4d2d0;font-family:"Ubuntu",sans-serif}
.main-nav a:last-child{border-right:0}
.main-nav a.active{color:var(--orange)}

.showcase{left:0;top:177px;width:1024px;height:268px;background:var(--band);border-top:2px solid #e2e0de;border-bottom:2px solid #e2e0de}
.slide{width:218px;height:147px;top:58px;background:#fff;padding:10px 9px;box-shadow:0 1px 3px rgba(0,0,0,.12)}
.slide::after{content:"";position:absolute;left:20px;right:20px;bottom:-14px;height:10px;border-radius:50%;background:rgba(0,0,0,.12);filter:blur(4px)}
.slide .photo{width:100%;height:100%}
.arrow{top:122px}
.dots{left:502px;top:232px;display:flex;gap:3px}
.dots span{width:7px;height:7px;border-radius:50%;background:#555}
.dots span:first-child{background:#999}

.feature{width:212px;height:250px;top:478px;background:linear-gradient(#fbfbfb,#eceaea);box-shadow:0 2px 4px rgba(0,0,0,.2)}
.feature .ribbon{position:absolute;left:-9px;right:-10px;top:20px;height:39px;background:linear-gradient(#fbb543,#e8890f);color:#fff;font-family:"Ubuntu",sans-serif;font-size:20.5px;text-align:center;line-height:39px;box-shadow:0 2px 3px rgba(0,0,0,.25);letter-spacing:.5px}
.feature p{position:absolute;left:18px;right:18px;top:69px;font-size:13.2px;line-height:21.3px;text-align:justify}
.btn-more{position:absolute;left:57px;top:206px;width:98px;height:28px;border-radius:8px;background:linear-gradient(#fcb84a,#e6850c);border:1px solid #c97208;color:#fff;font-family:"Ubuntu",sans-serif;font-size:17px;text-align:center;line-height:26px;box-shadow:0 0 0 2px #f5e9d6}

.welcome{left:123px;top:770px;width:527px;height:312px;background:var(--card);border:1px solid #dedcda;border-radius:6px;box-shadow:0 2px 3px rgba(0,0,0,.12);padding:25px 21px 0 21px}
.welcome h1{font-family:"Ubuntu",sans-serif;font-weight:400;font-size:21px;color:var(--orange);padding:0 0 4px 0;border-bottom:1px solid #c9c7c5;margin-bottom:6px}
.welcome p{font-size:13.6px;line-height:21.3px;text-align:justify}
.welcome h2{font-family:"Ubuntu",sans-serif;font-weight:400;font-size:13.6px;color:var(--orange);line-height:21.3px;letter-spacing:.3px}

.login{left:679px;top:770px;width:221px;height:314px;background:var(--card);border:1px solid #dedcda;border-radius:6px;box-shadow:0 2px 3px rgba(0,0,0,.12);overflow:hidden}
.tab-label{position:absolute;left:0;width:100%;text-align:center;color:#fff;font-family:"Ubuntu",sans-serif;font-size:15.5px;font-weight:500}
.field{position:absolute;left:20px;width:179px;height:33px;border:1px solid #e2e0de;border-radius:6px;background:#f5f4f4;font-size:12.5px;color:#444;padding:8px 8px}
.btn-login{position:absolute;left:69px;top:167px;width:83px;height:32px;background:var(--orange);border-radius:2px;color:#fff;font-size:13px;text-align:center;line-height:32px;font-family:"Ubuntu",sans-serif}
.not-member{position:absolute;left:0;width:100%;top:223px;text-align:center;font-size:12.5px;color:#444}

.site-footer{left:0;top:1113px;width:1024px;height:87px;background:linear-gradient(var(--footer-top),var(--footer-bottom))}
.site-footer p{position:absolute;left:0;width:1058px;text-align:center;color:#eee;font-size:12px;font-family:"Ubuntu",sans-serif}
</style>
</head>
<body>

<div class="abs logo">Logo Here</div>

<nav class="abs main-nav">
  <a class="active" href="#" style="width:134px">Home</a>
  <a href="#" style="width:156px">About Us</a>
  <a href="#" style="width:149px">Find Job</a>
  <a href="#" style="width:177px">Register Here</a>
  <a href="#" style="width:168px">Contact Us</a>
</nav>

<section class="abs showcase">
  <svg class="abs arrow" style="left:122px" width="16" height="24" viewBox="0 0 16 24"><path d="M12 3 L4 12 L12 21" fill="none" stroke="#555" stroke-width="4"/></svg>
  <div class="abs slide" style="left:163px"><div class="photo" role="img" aria-label="Offshore oil platform at sea with a gas flare" style="background:linear-gradient(135deg,#5b8dc7,var(--photo-sea) 60%,#2c5790)"></div></div>
  <div class="abs slide" style="left:404px"><div class="photo" role="img" aria-label="Team of engineers in hard hats reviewing plans" style="background:linear-gradient(135deg,#e6e8ec,var(--photo-team) 60%,#9aa3b2)"></div></div>
  <div class="abs slide" style="left:648px"><div class="photo" role="img" aria-label="Oil pump jack under a cloudy sky" style="background:linear-gradient(180deg,#b7c8de,var(--photo-sky) 65%,#6d6a66)"></div></div>
  <svg class="abs arrow" style="left:888px" width="16" height="24" viewBox="0 0 16 24"><path d="M4 3 L12 12 L4 21" fill="none" stroke="#555" stroke-width="4"/></svg>
  <div class="abs dots"><span></span><span></span><span></span></div>
</section>

<div class="abs feature" style="left:127px">
  <div class="ribbon">About Us</div>
  <p>We need a design for the login page, about page, and inner pages of a recruitment site for an oil and gas company. Design should be modern, sleek, professional.</p>
  <div class="btn-more">More</div>
</div>
<div class="abs feature" style="left:410px">
  <div class="ribbon">Environment</div>
  <p>We need a design for the login page, about page, and inner pages of a recruitment site for an oil and gas company. Design should be modern, sleek, professional.</p>
  <div class="btn-more">More</div>
</div>
<div class="abs feature" style="left:684px">
  <div class="ribbon">Job Seeker</div>
  <p>We need a design for the login page, about page, and inner pages of a recruitment site for an oil and gas company. Design should be modern, sleek, professional.</p>
  <div class="btn-more">More</div>
</div>

<section class="abs welcome">
  <h1>Welcome to our site</h1>
  <p>We need a design for the login page, about page, and inner pages of a recruitment site for an oil and gas company. Design should be modern, sleek, professional. We need a design for the login page, about page, and inner pages of a recruitment site for an oil and gas company. Design should be modern, sleek, professional. We need a design for the login page, about page, and inner pages of a recruitment site for an oil and gas company. Design should be modern, sleek, professional.</p>
  <h2>Our Great Work Environment:</h2>
  <p>We need a design for the login page, about page, and inner pages of a recruitment site for an oil and gas company. Design should be modern, sleek, professional.</p>
</section>

<section class="abs login">
  <svg class="abs" style="left:38px;top:-1px" width="150" height="62" viewBox="0 0 150 62">
    <path d="M2 0 H148 L126 52 Q122 60 112 60 H38 Q28 60 24 52 Z" fill="#fff" stroke="#e2e0de"/>
    <path d="M8 0 H142 L122 48 Q118 55 110 55 H40 Q32 55 28 48 Z" fill="url(#tabTop)"/>
    <defs><linearGradient id="tabTop" x1="0" y1="0" x2="0" y2="1"><stop offset="0" stop-color="#f6a52e"/><stop offset="1" stop-color="#cf6f08"/></linearGradient>
    <linearGradient id="tabBottom" x1="0" y1="0" x2="0" y2="1"><stop offset="0" stop-color="#f0a02a"/><stop offset="1" stop-color="#e07d0b"/></linearGradient></defs>
  </svg>
  <div class="tab-label" style="top:22px">Login Now</div>
  <div class="field" style="top:78px">User Name</div>
  <div class="field" style="top:123px">Password</div>
  <div class="btn-login">Login</div>
  <div class="not-member">Not a Member?</div>
  <svg class="abs" style="left:18px;top:251px" width="186" height="64" viewBox="0 0 186 64">
    <path d="M0 64 L22 12 Q27 2 38 2 H148 Q159 2 164 12 L186 64 Z" fill="#fff" stroke="#e2e0de"/>
    <path d="M8 64 L28 17 Q32 8 42 8 H144 Q154 8 158 17 L178 64 Z" fill="url(#tabBottom)"/>
  </svg>
  <div class="tab-label" style="top:279px">Register Here</div>
</section>

<footer class="abs site-footer">
  <p style="top:25px">Copyright @ 2012, All rights reserved.</p>
  <p style="top:41px">Terms &amp; Privacy Policy</p>
  <svg class="abs" style="left:754px;top:-2px" width="88" height="69" viewBox="0 0 88 69" role="img" aria-label="Social links">
    <path d="M0 0 H42 V68 L21 58 L0 68 Z" fill="#e4860f" stroke="#b96a08"/>
    <path d="M46 0 H88 V68 L67 58 L46 68 Z" fill="#e4860f" stroke="#b96a08"/>
    <rect x="14" y="22" width="14" height="14" fill="#3a3a3a"/>
    <rect x="60" y="22" width="14" height="14" fill="#3a3a3a"/>
  </svg>
</footer>

</body>
</html>
```